Willow Cradle Pregnancy and Baby Massage

I need a web design for a new business, WILLOW CRADLE PREGNANCY AND BABY MASSAGE that I am in the process of setting up in the suburbs of Perth, Western Australia. The business is owned and operated by myself and my intention is to service Pregnant Mothers and Parents of Young Babies that would benefit from massage. I would like to have a "Home Page" and pages for "About Me", "Pregnancy Massage", "Baby Massage", a Pricing Page for Pregnancy Massage Sessions, a Pricing Page for Baby Massage Sessions, and a "Contact Me" page to allow clients to either contact me with queries or book available pregnancy massage sessions on a particular day of the week. I would also like a "News" page that would include articles I have written, news about new courses and a link to my Friendnest page (yet to be set up). I would like to keep the colour schemes similar to my logo design colours. I need the design to be easy to follow and to appeal to a younger audience (20's to mid 30's).
The target audience is pregnant mothers-to-be wishing to receive massage treatments, and new parents and grandparents of small babies that would like to learn how to massage their babies.
The look and feel should be modern, professional, elegant and feminine.
I need the design to be in a standard format such that I can update the content by myself ( and does not need specialised software) as the company and business progresses.

Target Market(s)

Contact Information for Business Card

Card should have rounded edges. Design should have the same "feel" as the website. Contact Details of my business address, mobile phone, email and website should be included.

Font styles to use
Script

Requirements
Must have
• Same colours as logo design. In cmyk system, the colours are: 20,60,0,0 which best result is pantone 681 and 40,40,0,0 which best result is pantone 2645. Card should include the logo design.

```html
<!DOCTYPE html>
<html lang="en">
<head>
<meta charset="utf-8">
<title>Willow Cradle Pregnancy and Baby Massage</title>
<link rel="stylesheet" href="https://fonts.googleapis.com/css2?family=Fira+Sans:wght@600;700&family=Open+Sans:wght@400;600&display=swap">
<style>
  :root {
    --pink: #b264a6;
    --lavender: #8479c0;
    --ink: #3c3c3c;
    --text: #444444;
    --muted: #666666;
    --grey-band: #efefef;
    --rule: #d6d6d6;
    --white: #ffffff;
  }
  * { box-sizing: border-box; margin: 0; padding: 0; }
  html, body { width: 866px; height: 1200px; overflow: hidden; background: var(--white); }
  body { font-family: "Open Sans", sans-serif; color: var(--text); }
  .page { position: relative; width: 866px; height: 1200px; overflow: hidden; }
  .backdrop { position: absolute; inset: 0; }

  .brand { position: absolute; display: flex; align-items: center; gap: 7px; }
  .brand-dot { width: 14px; height: 14px; border-radius: 50%; background: var(--pink); flex: none; }
  .brand-name { font-family: "Open Sans", sans-serif; font-weight: 600; color: var(--pink); font-size: 12px; line-height: 1.25; }
  .brand-header { left: 54px; top: 28px; }
  .brand-footer { left: 54px; top: 1044px; }

  .main-nav { position: absolute; top: 31px; left: 298px; display: flex; gap: 27px; font-size: 10px; }
  .main-nav a { color: var(--ink); text-decoration: none; }
  .main-nav a.active { color: var(--lavender); }

  .hero-title { position: absolute; left: 54px; top: 206px; font-family: "Fira Sans", sans-serif; font-weight: 700; font-size: 18.5px; line-height: 24.5px; color: var(--lavender); letter-spacing: 0.3px; }

  .photo { position: absolute; border-radius: 50%; }
  .photo-about { left: 88px; top: 434px; width: 256px; height: 256px; background: radial-gradient(circle at 50% 45%, #e8c0a8 0%, #d9805f 45%, #8d6a5a 100%); }
  .photo-vision { left: 522px; top: 804px; width: 256px; height: 256px; background: radial-gradient(circle at 50% 45%, #eac7b2 0%, #b98a76 45%, #5e4a3c 100%); }

  .section-title { font-family: "Fira Sans", sans-serif; font-weight: 600; font-size: 18.5px; line-height: 22px; color: var(--ink); letter-spacing: 0.3px; }
  .section-title .accent-pink { color: var(--pink); }
  .section-title .accent-lavender { color: var(--lavender); }
  .body-copy { font-size: 11px; line-height: 18.5px; color: var(--text); }
  .body-copy p + p { margin-top: 5px; }

  .about { position: absolute; left: 379px; top: 574px; width: 420px; }
  .about .body-copy { margin-top: 18px; }
  .divider { position: absolute; left: 54px; top: 733px; width: 759px; height: 1px; background: var(--rule); }
  .vision { position: absolute; left: 54px; top: 770px; width: 470px; }
  .vision .body-copy { margin-top: 14px; }

  .copyright { position: absolute; left: 54px; top: 1113px; font-size: 9.5px; line-height: 13.5px; color: var(--muted); }
  .footer-col { position: absolute; top: 1034px; font-size: 9.5px; color: var(--ink); }
  .footer-col h3 { font-family: "Fira Sans", sans-serif; font-weight: 600; font-size: 10.5px; color: var(--pink); letter-spacing: 0.4px; margin-bottom: 5px; }
  .footer-col ul { list-style: none; }
  .site-map { left: 256px; }
  .site-map li { line-height: 18px; }
  .follow { left: 381px; }
  .follow li { display: flex; align-items: center; gap: 13px; height: 25.4px; }
  .follow .icon { width: 9px; height: 9px; border-radius: 50%; background: var(--ink); }
  .certified-label { position: absolute; left: 552px; top: 1128px; font-family: "Fira Sans", sans-serif; font-weight: 600; font-size: 10.5px; color: var(--pink); letter-spacing: 0.4px; }
  .cert-badge { position: absolute; left: 642px; top: 1088px; width: 160px; height: 92px; border-radius: 6px; background: #f3e6f1; }
</style>
</head>
<body>
<div class="page">
  <svg class="backdrop" width="866" height="1200" viewBox="0 0 866 1200" aria-hidden="true">
    <defs>
      <linearGradient id="heroTone" x1="0" y1="0" x2="1" y2="1">
        <stop offset="0" stop-color="#ecebea"/>
        <stop offset="0.55" stop-color="#efd9c9"/>
        <stop offset="1" stop-color="#e9dfd6"/>
      </linearGradient>
    </defs>
    <path d="M0,585 C110,480 250,445 380,470 C520,500 620,545 730,532 C805,522 845,495 866,470 L866,1000 C820,1060 760,1072 700,1050 C560,1010 400,958 260,958 C150,958 60,1008 0,1045 Z" fill="var(--grey-band)"/>
    <path role="img" aria-label="Photo of a smiling mother holding her baby" d="M0,80 Q300,110 866,70 L866,380 C820,450 760,495 650,490 C540,482 440,400 290,405 C170,410 80,440 0,490 Z" fill="url(#heroTone)"/>
    <path d="M0,80 Q300,110 866,68" fill="none" stroke="var(--pink)" stroke-width="2.5"/>
  </svg>

  <header>
    <div class="brand brand-header">
      <span class="brand-dot"></span>
      <span class="brand-name">Willow Cradle<br>Pregnancy and Baby Massage</span>
    </div>
    <nav class="main-nav">
      <a class="active" href="#">Home</a>
      <a href="#">About Me</a>
      <a href="#">Pregnancy Massage</a>
      <a href="#">Baby Massage</a>
      <a href="#">Pricing</a>
      <a href="#">News</a>
      <a href="#">Contact Me</a>
    </nav>
  </header>

  <h1 class="hero-title">WE SERVE PREGNANT MOTHERS<br>AND PARENTS OF YOUNG BABIES THAT WOULD<br>BENEFIT FROM MASSAGE.</h1>

  <div class="photo photo-about" role="img" aria-label="Photo of two newborn twins wrapped in a coral blanket"></div>
  <section class="about">
    <h2 class="section-title">ABOUT <span class="accent-pink">WILLOW CRADLE</span><br><span class="accent-lavender">PREGNANCY &amp; BABY MASSAGE</span></h2>
    <div class="body-copy"><p>Willow Cradle Pregnancy and Baby Massage was launched in 2017, offering massage for pregnant women, and instruction of baby massage to parents, grandparents and carers.</p></div>
  </section>

  <div class="divider"></div>

  <section class="vision">
    <h2 class="section-title">MY <span class="accent-pink">VISION</span></h2>
    <div class="body-copy">
      <p>My vision is to provide a professional massage service to pregnant mothers and babies that also benefitsfrom my skills and experience as a midwife.</p>
      <p>My expectation is that after each session, my clients should leave feeling relaxed, calm,emotionally nurtured, soothed and supported.</p>
      <p>At all times, I will take the utmost care of your privacy, safety and comfort in what is a very personal, intimate time in your life.</p>
    </div>
  </section>
  <div class="photo photo-vision" role="img" aria-label="Photo of two sleeping newborn twins in a woven basket"></div>

  <footer>
    <div class="brand brand-footer">
      <span class="brand-dot"></span>
      <span class="brand-name">Willow Cradle<br>Pregnancy and Baby Massage</span>
    </div>
    <p class="copyright">Copyright © 2017. Company Name.<br>All Right Reserved</p>
    <div class="footer-col site-map">
      <h3>SITE MAP</h3>
      <ul>
        <li>Home</li><li>About Me</li><li>Pregnancy Massage</li><li>Baby Massage</li><li>Pricing</li><li>News</li><li>Contact Me</li>
      </ul>
    </div>
    <div class="footer-col follow">
      <h3>FOLLOW US</h3>
      <ul>
        <li><span class="icon"></span>Friendnest</li>
        <li><span class="icon"></span>Chirpline</li>
        <li><span class="icon"></span>Snapframe</li>
        <li><span class="icon"></span>Pinboardly</li>
        <li><span class="icon"></span>ClipStream</li>
      </ul>
    </div>
    <p class="certified-label">CERTIFIED BY</p>
    <div class="cert-badge" role="img" aria-label="Certification badge"></div>
  </footer>
</div>
</body>
</html>
```